Law Offices business card

Hi there, I'll need business card for the Law Offices of Colin Matheny. The information must convey his strategic approach and quick resolution to complex business litigation needs. Please emphasize Civil Litigation, Corporate Law, Business Governance and Real Estate Law. Colin has over 25 years of experience in these fields.The card should be modern and edgy and the message should be clear. Please consult his current website for ideas.

```html
<!DOCTYPE html>
<html lang="en">
<head>
<meta charset="utf-8">
<title>Law Offices of Colin Matheny – Business Card</title>
<link rel="stylesheet" href="https://fonts.googleapis.com/css2?family=Arimo:wght@400;700&family=Libre+Baskerville:wght@400;700&display=swap">
<style>
  :root {
    --stage: #3b3b3d;
    --ink: #050505;
    --brand-red: #c9504f;
    --accent-red: #b8302f;
    --paper: #ffffff;
    --soft-white: #f2f2f2;
    --muted: #9a9a9a;
  }
  * { box-sizing: border-box; margin: 0; padding: 0; }
  html, body { width: 1200px; height: 950px; overflow: hidden; }
  body { background: var(--stage); position: relative; font-family: "Arimo", Arial, sans-serif; }

  .card {
    position: absolute;
    width: 560px;
    height: 320px;
    border-radius: 4px;
    overflow: hidden;
    box-shadow: 0 18px 40px rgba(0,0,0,.45);
  }

  /* back side */
  .card-back { left: 90px; top: 110px; background: var(--ink); }
  .card-back .firm-mark {
    position: absolute; left: 0; right: 0; top: 112px;
    text-align: center;
    font-family: "Libre Baskerville", Georgia, serif;
    font-weight: 700; font-size: 22px; color: var(--brand-red);
    letter-spacing: .5px;
  }
  .card-back .web-line {
    position: absolute; left: 0; right: 0; top: 196px;
    display: flex; align-items: center; justify-content: center; gap: 14px;
  }
  .card-back .web-line .rule { width: 70px; height: 2px; background: var(--accent-red); }
  .card-back .web-line span {
    color: var(--muted); font-size: 12px; letter-spacing: 4px;
  }

  /* front side */
  .card-front { left: 550px; top: 520px; background: var(--brand-red); }
  .card-front .arc { position: absolute; inset: 0; }
  .firm-name {
    position: absolute; left: 34px; top: 178px;
    font-family: "Libre Baskerville", Georgia, serif;
    font-weight: 700; color: var(--paper);
  }
  .firm-name .lead { display: block; font-size: 12px; letter-spacing: 1px; text-transform: uppercase; margin-bottom: 4px; }
  .firm-name .name { display: block; font-size: 28px; line-height: 1.05; }
  .firm-name .suffix { font-size: 18px; }

  .person {
    position: absolute; right: 26px; top: 30px; text-align: right; color: var(--paper);
  }
  .person .holder { font-weight: 700; font-size: 16px; }
  .person .role { font-size: 11px; margin-top: 3px; }

  .contact {
    position: absolute; right: 22px; top: 122px;
    list-style: none; color: var(--soft-white); font-size: 12.5px; line-height: 17px; text-align: right;
  }
  .contact li { display: flex; justify-content: flex-end; align-items: center; gap: 6px; }
  .contact svg { width: 11px; height: 11px; flex: none; }
  .contact .no-icon::after { content: ""; width: 11px; }
</style>
</head>
<body>

<section class="card card-back" aria-label="Card back">
  <div class="firm-mark">Colin Matheny</div>
  <div class="web-line"><i class="rule"></i><span>www.mathenylaw.com</span><i class="rule"></i></div>
</section>

<section class="card card-front" aria-label="Card front">
  <svg class="arc" viewBox="0 0 560 320" aria-hidden="true">
    <circle cx="128" cy="360" r="278" fill="var(--paper)"/>
    <circle cx="116" cy="366" r="270" fill="var(--ink)"/>
  </svg>

  <div class="firm-name">
    <span class="lead">Law Offices of</span>
    <span class="name">Colin Matheny<span class="suffix">, PA</span></span>
  </div>

  <div class="person">
    <div class="holder">Mark Ellison</div>
    <div class="role">President</div>
  </div>

  <ul class="contact">
    <li class="no-icon">4127 Harbor Crest Lane</li>
    <li>Milford Glen, NY 11020
      <svg viewBox="0 0 12 12"><path d="M2 2h3l1 3-2 1a7 7 0 0 0 2 2l1-2 3 1v3c-5 1-9-3-8-8z" fill="var(--paper)"/></svg></li>
    <li>555 0142 7730
      <svg viewBox="0 0 12 12"><rect x="3" y="1" width="6" height="10" rx="1" fill="none" stroke="var(--paper)" stroke-width="1.3"/></svg></li>
    <li>555 0186 2291
      <svg viewBox="0 0 12 12"><rect x="1" y="4" width="10" height="6" fill="var(--paper)"/><rect x="3" y="1" width="6" height="3" fill="var(--paper)"/></svg></li>
    <li>555 0173 4408
      <svg viewBox="0 0 12 12"><rect x="1" y="3" width="10" height="7" fill="var(--paper)"/><rect x="3" y="5" width="6" height="1" fill="var(--brand-red)"/></svg></li>
    <li>mark@mathenylaw.com
      <svg viewBox="0 0 12 12"><rect x="1" y="3" width="10" height="7" fill="var(--paper)"/><path d="M1 3l5 4 5-4" fill="none" stroke="var(--brand-red)" stroke-width="1"/></svg></li>
    <li>www.mathenylaw.com
      <svg viewBox="0 0 12 12"><circle cx="6" cy="6" r="5" fill="var(--paper)"/><path d="M1 6h10M6 1v10" stroke="var(--brand-red)" stroke-width=".8"/></svg></li>
  </ul>
</section>

</body>
</html>
```